Hull Harbour Trade Website makeover

Hull Harbour Trade is in need of a makeover. It is feeling tired and needs a fresh new look and feel as well as being user friendly.

Hull Harbour Trade is an industry owned marketplace website for the sale of recreational boats, marina berths, chandlery, water craft like kayaks - anything related to recreation on the water. The main focus however is boats - new and used. The site is only available to industry businesses so no private sales are available on the site.

This approach ensures that the buyers know that title is guaranteed to all boats sold and that the businesses are reputable and stand behind their products.

The current site address is www.hullharbourtrade.com.au

Target Market(s)

The target market are people interested in outdoor recreation - boaters, kayakers, sailors, paddle boarders, those looking for marina berths for their boat and those looking for service providers.

It should appeal to families, males and females, sports oriented people, fishermen, and those just looking for a relaxing, outdoor, healthy lifestyle.

Requirements
Must have
• Be very user friendly, intuitive in terms of searching, be uncluttered, fresh and engaging.
• Marine recreation is about lifestyle, fun and relaxation. When people buy a boat they are buying into a desirable, healthy lifestyle.
• It must present as professional and give consumers confidence about the professionalism of the businesses selling their products on the site.
Nice to have
• Good images that portray the lifestyle in the Australian marketplace.
• Cater for the needs of sellers to be able to showcase their products to consumers.
Should not have
• Be cluttered and hard to navigate.

```html
<!DOCTYPE html>
<html lang="en">
<head>
<meta charset="utf-8">
<title>Hull Harbour Trade – Members Say</title>
<link rel="stylesheet" href="https://fonts.googleapis.com/css2?family=Fira+Sans:ital,wght@0,500;0,600;0,900;1,400;1,500&display=swap">
<style>
  :root {
    --page-bg: #f6f6f6;
    --heading: #a8a8a8;
    --rule: #c4c4c4;
    --quote-text: #a9a9a9;
    --quote-mark: #bdbdbd;
    --author: #6aaee0;
    --ring: #dcdcdc;
    --ring-inner: #ffffff;
    --photo-a: #e9e4df;
    --photo-b: #d7c7b8;
    --footer-line: #dedede;
  }
  * { box-sizing: border-box; margin: 0; padding: 0; }
  html, body { width: 1200px; height: 900px; overflow: hidden; }
  body {
    position: relative;
    background: radial-gradient(ellipse at 50% 40%, #fbfbfb 0%, var(--page-bg) 70%);
    font-family: "Fira Sans", Arial, sans-serif;
  }
  .section-title {
    position: absolute;
    top: 59px; left: 0; width: 1200px;
    text-align: center;
    font-weight: 500;
    font-size: 25px;
    line-height: 32px;
    letter-spacing: -0.5px;
    color: var(--heading);
    text-shadow: 0 1px 0 #fff, 0 -1px 0 rgba(0,0,0,0.08);
  }
  .title-rule {
    position: absolute;
    top: 74px; height: 3px; width: 280px;
  }
  .title-rule--left { left: 180px; background: linear-gradient(to right, rgba(196,196,196,0), var(--rule) 60%); }
  .title-rule--right { left: 721px; background: linear-gradient(to left, rgba(196,196,196,0), var(--rule) 60%); }

  .avatar {
    position: absolute;
    width: 170px; height: 170px;
    border-radius: 50%;
    background: var(--ring);
    padding: 9px;
    box-shadow: inset 0 1px 2px rgba(0,0,0,0.08);
  }
  .avatar-photo {
    width: 100%; height: 100%;
    border-radius: 50%;
    background: radial-gradient(circle at 50% 40%, var(--photo-b) 0%, var(--photo-a) 55%, var(--ring-inner) 100%);
  }
  .quote-mark {
    position: absolute;
    font-weight: 900;
    font-size: 74px;
    line-height: 1;
    color: var(--quote-mark);
  }
  .quote-text {
    position: absolute;
    font-style: italic;
    font-weight: 400;
    font-size: 17.5px;
    line-height: 21.6px;
    color: var(--quote-text);
    white-space: nowrap;
  }
  .quote-author {
    position: absolute;
    font-style: italic;
    font-weight: 400;
    font-size: 13.5px;
    color: var(--author);
    text-align: right;
    white-space: nowrap;
  }
  .footer-line {
    position: absolute;
    left: 0; bottom: 0; width: 1200px; height: 3px;
    background: var(--footer-line);
  }
</style>
</head>
<body>
  <div class="title-rule title-rule--left"></div>
  <h2 class="section-title">MEMBERS SAY</h2>
  <div class="title-rule title-rule--right"></div>

  <!-- Testimonial 1 -->
  <div class="avatar" style="left:184px; top:134px;">
    <div class="avatar-photo" role="img" aria-label="Portrait photo of member Noah Brenner"></div>
  </div>
  <div class="quote-mark" style="left:396px; top:134px;">“</div>
  <p class="quote-text" style="left:445px; top:151px;">
    We found our first family cruiser here in a single weekend, and the<br>
    dealer walked us through every detail of the hull, engine and trailer.<br>
    Knowing every seller is an industry business gave us real confidence,<br>
    and title was guaranteed from day one. Now our Saturdays are spent<br>
    out on the bay with the kids, fishing rods and a picnic on board.
  </p>
  <p class="quote-author" style="right:201px; top:279px;">By Noah Brenner</p>

  <!-- Testimonial 2 -->
  <div class="quote-mark" style="left:195px; top:399px;">“</div>
  <p class="quote-text" style="left:243px; top:416px;">
    I was after a sea kayak and a paddle board for summer, and the search<br>
    filters took me straight to the right chandlery within minutes. The<br>
    listings were clear, the photos honest and the staff knew their gear.<br>
    Everything arrived ready for the water, and I was paddling the<br>
    harbour at sunrise the very next morning. Simple, fresh and easy.
  </p>
  <p class="quote-author" style="right:379px; top:544px;">By Lena Brenner</p>
  <div class="avatar" style="left:848px; top:400px;">
    <div class="avatar-photo" role="img" aria-label="Portrait photo of member Lena Brenner"></div>
  </div>

  <!-- Testimonial 3 -->
  <div class="avatar" style="left:184px; top:665px;">
    <div class="avatar-photo" role="img" aria-label="Portrait photo of member Mark Dalton"></div>
  </div>
  <div class="quote-mark" style="left:396px; top:664px;">“</div>
  <p class="quote-text" style="left:445px; top:681px;">
    Finding a marina berth close to home used to take months of calls.<br>
    Through the marketplace I compared berths, service providers and<br>
    prices side by side, then booked with a reputable operator that same<br>
    afternoon. My yacht is now moored five minutes away, and weekend<br>
    sailing has become a relaxed, healthy habit for the whole family.
  </p>
  <p class="quote-author" style="right:176px; top:809px;">By Mark Dalton</p>

  <div class="footer-line"></div>
</body>
</html>
```